4D Cradle Glimpse Luxury Ultrasound Billboard

Design a HIGH-END, MODERN billboard for my private prenatal ultrasound studio, 4D Cradle Glimpse, located in Pace, Florida.
This billboard will be viewed by drivers traveling at highway speeds, so it must be extremely clean, simple, and readable within 6 seconds.
About My Business
4D Cradle Glimpse is a private prenatal ultrasound studio specializing in:
Highest technology 4D/HD Ultrasounds
Early Gender Determination
Pregnancy Confirmation
I have been serving families for nearly 10 years and is known for creating a memorable experience, not just an ultrasound appointment.
Design Style
I DO NOT want:
Flowers
Leaves
Swirls
Glitter
Hearts everywhere
Busy backgrounds
Generic maternity stock graphics
I DO want:
Modern
Luxury
Upscale
Clean
Professional
Eye-catching
Premium medical spa feel
Colors
Use colors from my logo:
LOGO Green ( or a deep green)
Black
White
Soft Gold accents
Images:
Incorporate my professional headshot in a clean, modern way, logo, and the ultrasound images
Text
Keep wording minimal.
Primary Headline ( OPEN TO IDEAS) :
EXAMPLES ( WOULD RATHER SOMETHING MORE CATCHY)
" ADVANCED IMAGING. UNFORGETTABLE MOMENTS"
"MEET YOUR BABY BEFORE BIRTH"
Under headline:
4D Ultrasound • Early Gender • Pregnancy Confirmation
Business Name:
4D Cradle Glimpse
Private Prenatal Ultrasound Studio
Phone Number:
850-471-5923
Important
This billboard must be readable in 5–6 seconds from a moving vehicle.
Less text is better.
The phone number and business name must be visible from a distance.
The design should feel like a premium brand that immediately tells expecting parents:
“This is where I go to see my baby.”
Files Provided
Official logo
Headshot
Ultrasound images
Don’t make this look like a medical office billboard.
Make it look like a luxury baby experience billboard. That’s what separates 4D Cradle Glimpse from hospitals, OB offices, and all the new studios popping up around you. The emotional connection is what gets moms to book. ❤️
Billboard Size - 10.6” x 36”

```html
<!DOCTYPE html>
<html lang="en">
<head>
<meta charset="utf-8">
<title>4D Cradle Glimpse Billboard</title>
<link href="https://fonts.googleapis.com/css2?family=Fira+Sans+Extra+Condensed:wght@700&family=Fira+Sans+Condensed:wght@600;800&family=Ubuntu:wght@700&family=Roboto+Condensed:wght@700&display=swap" rel="stylesheet">
<style>
  :root {
    --page: #eef1f5;
    --frame: #1c1c1e;
    --cream-light: #f5ece0;
    --cream: #ead9c1;
    --cream-deep: #dcc4a1;
    --gold: #c09a55;
    --charcoal: #2f3235;
    --ink: #2b2e33;
    --white: #ffffff;
    --green: #2f4a36;
  }
  * { box-sizing: border-box; margin: 0; padding: 0; }
  html, body { width: 1200px; height: 1200px; overflow: hidden; }
  body { background: var(--page); position: relative; }

  .billboard {
    position: absolute; left: 20px; top: 744px;
    width: 1169px; height: 363px;
    background: var(--frame);
  }
  .billboard__face {
    position: absolute; left: 16px; top: 16px; right: 14px; bottom: 14px;
    background: linear-gradient(100deg, var(--cream-light) 0%, var(--cream) 55%, var(--cream-deep) 100%);
    overflow: hidden;
  }
  .contact-band {
    position: absolute; left: 0; right: 0; bottom: 0; height: 83px;
    background: var(--charcoal);
  }

  .headshot {
    position: absolute; left: 55px; top: 14px; width: 207px; height: 320px;
    border-radius: 90px 90px 0 0;
    background: linear-gradient(180deg, #d8bf97 0%, #c9a77c 35%, #35503c 70%, #2c4232 100%);
  }
  .scan-image {
    position: absolute; left: 928px; top: 30px; width: 182px; height: 126px;
    border: 6px solid var(--charcoal); border-radius: 10px;
    background: linear-gradient(90deg, #d9a79a 0%, #c98d82 50%, #d9a79a 100%);
  }
  .scan-machine {
    position: absolute; left: 895px; top: 162px; width: 190px; height: 88px;
    border-radius: 16px 16px 4px 4px;
    background: linear-gradient(180deg, #4a4d52 0%, #c9c9c6 55%, #e4e3df 100%);
  }

  .probe-lines { position: absolute; left: 0; top: 0; width: 1139px; height: 333px; }

  .headline {
    position: absolute; left: 250px; width: 660px; text-align: center;
    color: var(--gold); text-transform: uppercase; white-space: nowrap;
    text-shadow: 1px 1px 0 var(--white);
  }
  .headline--top {
    top: 10px; font: 700 38px/1 "Fira Sans Extra Condensed", sans-serif;
    letter-spacing: -0.5px;
  }
  .headline--main {
    top: 50px; font: 800 42px/1 "Fira Sans Condensed", sans-serif;
  }

  .services {
    position: absolute; left: 387px; top: 94px; list-style: none;
    font: 700 42px/46px "Ubuntu", sans-serif; color: var(--ink);
    text-shadow: 1px 1px 0 var(--white); white-space: nowrap;
  }

  .phone {
    position: absolute; left: 310px; top: 262px; height: 58px;
    display: flex; align-items: center; gap: 12px;
    font: 700 58px/1 "Roboto Condensed", sans-serif; color: var(--white);
    white-space: nowrap;
  }
  .phone__icon { width: 46px; height: 46px; flex: none; }

  .tagline-pill {
    position: absolute; left: 737px; top: 266px; width: 383px; height: 50px;
    border-radius: 25px; background: var(--white);
    display: flex; align-items: center; justify-content: center;
    font: 600 24px/1 "Fira Sans Condensed", sans-serif; color: var(--ink);
    white-space: nowrap;
  }

  .brand-badge {
    position: absolute; left: 17px; top: 264px; width: 118px; height: 58px;
    border-radius: 8px; background: var(--white); border: 2px solid #cfc4b3;
    display: flex; align-items: center; justify-content: center; gap: 5px;
  }
  .brand-badge__dot { width: 8px; height: 8px; border-radius: 50%; background: var(--gold); }
  .brand-badge__name {
    font: 700 13px/1.05 "Ubuntu", sans-serif; color: var(--green); text-align: center;
  }
</style>
</head>
<body>
  <section class="billboard" aria-label="4D Cradle Glimpse billboard">
    <div class="billboard__face">
      <div class="contact-band"></div>

      <svg class="probe-lines" viewBox="0 0 1139 333" aria-hidden="true">
        <g stroke="#ffffff" stroke-width="1.5" fill="none">
          <line x1="263" y1="291" x2="365" y2="135"/>
          <line x1="263" y1="291" x2="365" y2="176"/>
          <line x1="263" y1="291" x2="365" y2="207"/>
        </g>
        <g fill="#ffffff">
          <circle cx="365" cy="135" r="3"/>
          <circle cx="365" cy="176" r="3"/>
          <circle cx="365" cy="207" r="3"/>
        </g>
      </svg>

      <div class="headshot" role="img" aria-label="Portrait of the studio owner holding an ultrasound probe"></div>
      <div class="scan-image" role="img" aria-label="4D ultrasound image of twin babies on a monitor"></div>
      <div class="scan-machine" role="img" aria-label="Ultrasound machine console"></div>

      <h2 class="headline headline--top">Advanced Imaging. Unforgettable Moments</h2>
      <h1 class="headline headline--main">Meet Your Baby Before Birth</h1>

      <ul class="services">
        <li>4D Ultrasound</li>
        <li>Early Gender</li>
        <li>Pregnancy Confirmation</li>
      </ul>

      <div class="brand-badge">
        <span class="brand-badge__dot"></span>
        <span class="brand-badge__name">4D Cradle<br>Glimpse</span>
      </div>

      <div class="phone">
        <svg class="phone__icon" viewBox="0 0 46 46" aria-hidden="true">
          <circle cx="23" cy="23" r="23" fill="#ffffff"/>
          <path d="M17 12h7l-2 7h-3l-2 8h3l-2 7h-6c-1-8 2-17 5-22z" fill="#2f3235"/>
        </svg>
        <span>850-471-5923</span>
      </div>

      <div class="tagline-pill">Private Prenatal Ultrasound Studio</div>
    </div>
  </section>
</body>
</html>
```